Professional & attention grabbing.

A business card design, front and back. I already have a logo I will attach, but I am open to something new as well.
Things to include:
Name:
Title:
Phone:
Email:
Wanting something that is professional but attention grabbing.
Also we do a lot of work using drones on natural gas pipelines (leading the future)if you want to include any of that. I'm open to ideas.
Target Market(s)
Natural gas transmission industry / greenhouse gas mitigation industry
Industry/Entity Type
Business
Colors
Designer to choose colors to be used in the design.
Look and feel
Each slider illustrates characteristics of the customer's brand and the style your logo design should communicate.

```html
<!DOCTYPE html>
<html lang="en">
<head>
<meta charset="utf-8">
<title>Halden Inspections — Business Card</title>
<link rel="stylesheet" href="https://fonts.googleapis.com/css2?family=Open+Sans:wght@400;600;700&display=swap">
<style>
  :root {
    --bg: #e6e6e6;
    --card-white: #ffffff;
    --ink: #3a3a3c;
    --ink-soft: #4a4a4c;
    --red: #c1232a;
    --rule: #cfcfcf;
    --back-dark: #3b3b3d;
    --back-mid: #4a4a4d;
  }
  * { margin: 0; padding: 0; box-sizing: border-box; }
  html, body {
    width: 1200px; height: 987px; overflow: hidden;
    background: var(--bg);
    font-family: "Open Sans", Arial, sans-serif;
  }
  .canvas { position: relative; width: 1200px; height: 987px; }

  .card {
    position: absolute; left: 293px; width: 615px; height: 352px;
    box-shadow: 0 2px 6px rgba(0,0,0,0.18);
    overflow: hidden;
  }
  .card--front { top: 130px; background: var(--card-white); }
  .card--back { top: 505px; background: var(--back-dark); }

  /* front */
  .brand {
    position: absolute; left: 62px; top: 82px;
    display: flex; align-items: center; gap: 12px;
  }
  .brand__square { width: 30px; height: 30px; background: var(--red); }
  .brand__name {
    font-size: 38px; font-weight: 700; color: var(--ink);
    letter-spacing: 0.5px; line-height: 1;
  }
  .brand__sub {
    position: absolute; left: 104px; top: 168px;
    font-size: 11px; font-weight: 700; color: var(--ink);
    letter-spacing: 0.6px;
  }
  .divider {
    position: absolute; left: 325px; top: 101px;
    width: 1px; height: 150px; background: var(--rule);
  }
  .contact { position: absolute; left: 359px; top: 106px; color: var(--ink-soft); }
  .contact__name {
    font-size: 21px; font-weight: 600; color: var(--red);
    letter-spacing: 0.3px; line-height: 1.2;
  }
  .contact__title { font-size: 17px; line-height: 1.3; margin-bottom: 12px; }
  .contact__list { list-style: none; }
  .contact__item {
    display: flex; align-items: center; gap: 8px;
    font-size: 16px; line-height: 23.5px;
  }
  .contact__icon { width: 14px; height: 14px; flex: none; }

  .front-rule {
    position: absolute; left: 0; top: 318px; width: 100%; height: 2px;
    background: var(--ink);
  }
  .front-band {
    position: absolute; left: 0; bottom: 0; width: 100%; height: 25px;
    background: var(--red);
  }

  /* back */
  .back-pattern {
    position: absolute; inset: 0;
    background: linear-gradient(135deg, var(--back-mid), var(--back-dark) 60%, var(--back-mid));
  }
  .back-mark {
    position: absolute; right: 38px; bottom: 38px;
    display: flex; align-items: center; gap: 8px;
  }
  .back-mark__square { width: 18px; height: 18px; background: var(--red); }
  .back-mark__name {
    font-size: 22px; font-weight: 700; color: var(--card-white);
    letter-spacing: 0.5px;
  }
</style>
</head>
<body>
<main class="canvas">
  <section class="card card--front" aria-label="Card front">
    <div class="brand">
      <span class="brand__square"></span>
      <span class="brand__name">HALDEN</span>
    </div>
    <div class="brand__sub">HALDEN INSPECTIONS</div>

    <div class="divider"></div>

    <div class="contact">
      <p class="contact__name">MARK ELLISON</p>
      <p class="contact__title">CEO/Founder</p>
      <ul class="contact__list">
        <li class="contact__item">
          <svg class="contact__icon" viewBox="0 0 24 24" aria-hidden="true"><path fill="#c1232a" d="M6.6 10.8a15.1 15.1 0 0 0 6.6 6.6l2.2-2.2a1 1 0 0 1 1-.25 11.4 11.4 0 0 0 3.6.57 1 1 0 0 1 1 1V20a1 1 0 0 1-1 1A17 17 0 0 1 3 4a1 1 0 0 1 1-1h3.5a1 1 0 0 1 1 1c0 1.25.2 2.45.57 3.57a1 1 0 0 1-.25 1z"/></svg>
          555 210 4837
        </li>
        <li class="contact__item">
          <svg class="contact__icon" viewBox="0 0 24 24" aria-hidden="true"><rect x="2" y="5" width="20" height="14" fill="#c1232a"/><path d="M2 5l10 8 10-8" fill="none" stroke="#fff" stroke-width="1.8"/></svg>
          mark@haldeninspect.com
        </li>
        <li class="contact__item">
          <svg class="contact__icon" viewBox="0 0 24 24" aria-hidden="true"><circle cx="12" cy="12" r="10" fill="#c1232a"/><path d="M2 12h20M12 2c3 3 3 17 0 20M12 2c-3 3-3 17 0 20" fill="none" stroke="#fff" stroke-width="1.5"/></svg>
          www.haldeninspect.com
        </li>
      </ul>
    </div>

    <div class="front-rule"></div>
    <div class="front-band"></div>
  </section>

  <section class="card card--back" aria-label="Card back">
    <div class="back-pattern" role="img" aria-label="Tiled repeat of the brand symbol in dark greys"></div>
    <div class="back-mark">
      <span class="back-mark__square"></span>
      <span class="back-mark__name">HALDEN</span>
    </div>
  </section>
</main>
</body>
</html>
```